Banner ad series

We need a series of banner ads for 4 different digital products. The ads will drive traffic to these landing pages:
Relocate.set: http://pinnedtidygoods.example/relocatekit/
Treasures.file: http://pinnedtidygoods.example/digital-treasures-file/
Jumpstart Drill School: http://pinnedtidygoods.example/jumpstart-drill-school/
Vital Habits Drill School: http://pinnedtidygoods.example/vital-habits/

Banner Ad Sizes needed:
160x600, 728x90, 300x250

Text files with the copy/variations needed for each product are attached. In the text file - the first line of each option is the main headline. All other copy is support copy and OPTIONAL.

Target Market(s)

Our target market is a woman between the ages of 30-55 with kids. She's smart, working professionally and always on the lookout for products and services that will help her get more organized.

Industry/Entity Type

Digital

Requirements
Must have
• Pinned Tidy logo

```html
<!DOCTYPE html>
<html lang="en">
<head>
<meta charset="utf-8">
<title>Pinned Tidy – Jumpstart Drill School Banner Set</title>
<link rel="stylesheet" href="https://fonts.googleapis.com/css2?family=Open+Sans:wght@400;600;700;800&display=swap">
<style>
  :root {
    --backdrop: #4a2c1a;
    --green-dark: #2b8a14;
    --green-light: #4cab2a;
    --green-rim: #8fd35a;
    --white: #ffffff;
    --brand-ink: #2b8a14;
    --orange-top: #ffa63a;
    --orange-bottom: #ea5f0c;
    --ink: #111111;
    --photo-a: #eef0ec;
    --photo-b: #c9cfc4;
    --photo-c: #9fb08a;
  }
  * { box-sizing: border-box; margin: 0; padding: 0; }
  html, body { width: 1200px; height: 800px; overflow: hidden; background: var(--backdrop); }
  body { font-family: "Open Sans", Arial, sans-serif; }

  .stage {
    position: absolute; left: 0; top: 0;
    width: 1050px; height: 700px;
    transform: scale(1.142857); transform-origin: 0 0;
  }
  .banner { position: absolute; overflow: hidden; background: var(--white); }
  .banner--skyscraper { left: 64px; top: 25px; width: 160px; height: 600px; }
  .banner--rect-a { left: 250px; top: 75px; width: 300px; height: 250px; }
  .banner--rect-b { left: 574px; top: 75px; width: 300px; height: 250px; }
  .banner--leaderboard { left: 250px; top: 358px; width: 728px; height: 90px; }

  .banner__photo {
    position: absolute;
    background: linear-gradient(160deg, var(--photo-a) 0%, var(--photo-b) 55%, var(--photo-c) 100%);
  }
  .banner__shape { position: absolute; left: 0; top: 0; }

  .logo {
    position: absolute; background: var(--white);
    display: flex; align-items: center; justify-content: center;
  }
  .logo__name { color: var(--brand-ink); font-weight: 700; font-size: 18px; letter-spacing: .2px; white-space: nowrap; }

  .copy { position: absolute; color: var(--white); text-align: center; }
  .copy__head { font-weight: 700; line-height: 1.1; text-transform: uppercase; white-space: nowrap; }
  .insert { position: relative; display: inline-block; width: 1.1em; text-align: center; }
  .insert__word {
    position: absolute; left: 50%; top: -0.85em; transform: translateX(-50%);
    font-size: .6em; text-transform: none; font-weight: 700;
  }
  .insert__caret { font-weight: 700; font-size: .75em; position: relative; top: .2em; }
  .rule { border: 0; border-top: 1px dotted rgba(255,255,255,.7); margin: 8px auto; width: 82%; }
  .copy__body { font-weight: 400; line-height: 1.3; letter-spacing: -.2px; white-space: nowrap; }

  .cta {
    position: absolute; display: flex; align-items: center; justify-content: center; gap: 8px;
    border-radius: 16px; color: var(--white); font-weight: 700;
    background: linear-gradient(var(--orange-top), var(--orange-bottom));
    border: 1.5px solid #fff3e0;
    box-shadow: 0 1px 3px rgba(0,0,0,.35);
  }
  .cta__icon { width: 22px; height: 22px; }
</style>
</head>
<body>
<main class="stage">

  <!-- 160 x 600 -->
  <section class="banner banner--skyscraper" aria-label="Skyscraper banner">
    <div class="banner__photo" style="left:0;top:66px;width:160px;height:280px" role="img" aria-label="Photo of a tidy wall organiser with mail pockets, notes and hooks"></div>
    <svg class="banner__shape" width="160" height="600" viewBox="0 0 160 600">
      <defs>
        <linearGradient id="skyGreen" x1="0" y1="0" x2="0" y2="1">
          <stop offset="0" stop-color="var(--green-light)"/><stop offset="1" stop-color="var(--green-dark)"/>
        </linearGradient>
      </defs>
      <path d="M0 318 Q80 298 160 306 V600 H0 Z" fill="var(--green-rim)"/>
      <path d="M0 328 Q80 310 160 318 V600 H0 Z" fill="url(#skyGreen)"/>
    </svg>
    <div class="logo" style="left:0;top:0;width:160px;height:66px">
      <span class="logo__name">Pinned Tidy</span>
    </div>
    <div class="copy" style="left:0;top:330px;width:160px">
      <p class="copy__head" style="font-size:19px">Now that it's</p>
      <p class="copy__head" style="font-size:15px;margin-top:8px">The <span class="insert"><span class="insert__word">New</span><span class="insert__caret">^</span></span> New Year</p>
      <hr class="rule" style="margin-top:12px">
      <p class="copy__head" style="font-size:17px;margin-top:12px">It's time to<br>get organized!</p>
      <hr class="rule" style="margin-top:12px">
      <p class="copy__body" style="font-size:12px;margin-top:10px">Sign Up for the Jumpstart<br>Drill School &amp; Organize<br>your home AND your life</p>
    </div>
    <a class="cta" style="left:7px;top:552px;width:147px;height:34px;font-size:14.5px">Learn More!
      <svg class="cta__icon" viewBox="0 0 22 22"><circle cx="11" cy="11" r="10" fill="var(--ink)"/><path d="M9 6.5 L13.5 11 L9 15.5" stroke="#fff" stroke-width="2.4" fill="none" stroke-linecap="round" stroke-linejoin="round"/></svg>
    </a>
  </section>

  <!-- 300 x 250 (A) -->
  <section class="banner banner--rect-a" aria-label="Medium rectangle banner">
    <div class="banner__photo" style="left:140px;top:0;width:160px;height:250px" role="img" aria-label="Photo of a tidy wall organiser with mail pockets and a lamp"></div>
    <svg class="banner__shape" width="300" height="250" viewBox="0 0 300 250">
      <defs>
        <linearGradient id="rectGreenA" x1="0" y1="0" x2="0" y2="1">
          <stop offset="0" stop-color="var(--green-light)"/><stop offset="1" stop-color="var(--green-dark)"/>
        </linearGradient>
      </defs>
      <path d="M0 0 H214 Q150 90 164 250 H0 Z" fill="var(--green-rim)"/>
      <path d="M0 0 H206 Q142 90 156 250 H0 Z" fill="url(#rectGreenA)"/>
    </svg>
    <div class="logo" style="left:0;top:0;width:154px;height:66px">
      <span class="logo__name">Pinned Tidy</span>
    </div>
    <div class="copy" style="left:0;top:78px;width:154px">
      <p class="copy__head" style="font-size:18px">Now that it's</p>
      <p class="copy__head" style="font-size:14px;margin-top:6px">The <span class="insert"><span class="insert__word">New</span><span class="insert__caret">^</span></span> New Year</p>
      <hr class="rule" style="margin:7px auto">
      <p class="copy__head" style="font-size:16px">It's time to<br>get organized!</p>
      <hr class="rule" style="margin:7px auto">
      <p class="copy__body" style="font-size:11.5px;line-height:1.28">Sign Up for the Jumpstart<br>Drill School &amp; Organize<br>your home AND your life</p>
    </div>
    <a class="cta" style="left:154px;top:206px;width:140px;height:31px;font-size:14px">Learn More!
      <svg class="cta__icon" viewBox="0 0 22 22"><circle cx="11" cy="11" r="10" fill="var(--ink)"/><path d="M9 6.5 L13.5 11 L9 15.5" stroke="#fff" stroke-width="2.4" fill="none" stroke-linecap="round" stroke-linejoin="round"/></svg>
    </a>
  </section>

  <!-- 300 x 250 (B) -->
  <section class="banner banner--rect-b" aria-label="Medium rectangle banner, variant">
    <div class="banner__photo" style="left:140px;top:0;width:160px;height:250px" role="img" aria-label="Photo of a tidy wall organiser with mail pockets and a lamp"></div>
    <svg class="banner__shape" width="300" height="250" viewBox="0 0 300 250">
      <defs>
        <linearGradient id="rectGreenB" x1="0" y1="0" x2="0" y2="1">
          <stop offset="0" stop-color="var(--green-light)"/><stop offset="1" stop-color="var(--green-dark)"/>
        </linearGradient>
      </defs>
      <path d="M0 0 H214 Q150 90 164 250 H0 Z" fill="var(--green-rim)"/>
      <path d="M0 0 H206 Q142 90 156 250 H0 Z" fill="url(#rectGreenB)"/>
    </svg>
    <div class="logo" style="left:0;top:0;width:154px;height:66px">
      <span class="logo__name">Pinned Tidy</span>
    </div>
    <div class="copy" style="left:0;top:78px;width:154px">
      <p class="copy__head" style="font-size:18px">Now that it's</p>
      <p class="copy__head" style="font-size:14px;margin-top:6px">The <span class="insert"><span class="insert__word">New</span><span class="insert__caret">^</span></span> New Year</p>
      <hr class="rule" style="margin:7px auto">
      <p class="copy__head" style="font-size:16px">It's time to<br>get organized!</p>
      <hr class="rule" style="margin:7px auto">
      <p class="copy__body" style="font-size:11.5px;line-height:1.28">Sign Up for the Jumpstart<br>Drill School &amp; Organize<br>your home AND your life</p>
    </div>
    <a class="cta" style="left:154px;top:206px;width:140px;height:31px;font-size:14px">Learn More!
      <svg class="cta__icon" viewBox="0 0 22 22"><circle cx="11" cy="11" r="10" fill="var(--ink)"/><path d="M9 6.5 L13.5 11 L9 15.5" stroke="#fff" stroke-width="2.4" fill="none" stroke-linecap="round" stroke-linejoin="round"/></svg>
    </a>
  </section>

  <!-- 728 x 90 -->
  <section class="banner banner--leaderboard" aria-label="Leaderboard banner">
    <div class="banner__photo" style="left:470px;top:0;width:258px;height:90px" role="img" aria-label="Photo of a wall organiser with labelled mail pockets"></div>
    <svg class="banner__shape" width="728" height="90" viewBox="0 0 728 90">
      <defs>
        <linearGradient id="boardGreen" x1="0" y1="0" x2="0" y2="1">
          <stop offset="0" stop-color="var(--green-light)"/><stop offset="1" stop-color="var(--green-dark)"/>
        </linearGradient>
      </defs>
      <path d="M150 0 H530 Q478 40 494 90 H150 Z" fill="var(--green-rim)"/>
      <path d="M150 0 H522 Q470 40 486 90 H150 Z" fill="url(#boardGreen)"/>
    </svg>
    <div class="logo" style="left:0;top:0;width:153px;height:90px">
      <span class="logo__name">Pinned Tidy</span>
    </div>
    <div class="copy" style="left:156px;top:6px;width:316px">
      <p class="copy__head" style="font-size:17px;margin-top:2px">Now that it's the <span class="insert"><span class="insert__word">New</span><span class="insert__caret">^</span></span> New Year</p>
      <p class="copy__head" style="font-size:19.5px;margin-top:1px">It's time to get organized!</p>
      <p class="copy__body" style="font-size:12px;line-height:1.15;margin-top:1px">Sign Up for the Jumpstart Drill School &amp; Organize your<br>home AND your life</p>
    </div>
    <a class="cta" style="left:555px;top:34px;width:150px;height:32px;font-size:14.5px">Learn More!
      <svg class="cta__icon" viewBox="0 0 22 22"><circle cx="11" cy="11" r="10" fill="var(--ink)"/><path d="M9 6.5 L13.5 11 L9 15.5" stroke="#fff" stroke-width="2.4" fill="none" stroke-linecap="round" stroke-linejoin="round"/></svg>
    </a>
  </section>

</main>
</body>
</html>
```